The Velvet Magpie business card

I need a business card for my makeup artist business. I specialise in bridal, glamour, formal and special occasion makeup.
I am a mobile makeup artist who caters for every from nowra to sydney.
I do the following services:
Bridal makeup
airbrush makeup
special occasion
formals
hens nights/ girls night
makeup lesson
makeup for all ages from flower girl to Nanna of the bride!
photoshoot makeup
SPFX

I would like the card to portray a very professional sleek makeup business. I would also like another version of the card directed especially towards brides.

Please see my website to understand colours etc www.thevelvetmagpie-example.com

The Velvet Magpie
Professional Makeup Artist
Lorraine Kedby
0491802643
info@thevelvetmagpie-example.com
www.thevelvetmagpie-example.com
www.facebook.com/thevelvetmagpie

```html
<!DOCTYPE html>
<html lang="en">
<head>
<meta charset="utf-8">
<title>The Velvet Magpie – Business Card</title>
<link rel="stylesheet" href="https://fonts.googleapis.com/css2?family=Ubuntu:wght@300;700&family=Roboto+Condensed:wght@400;700&display=swap">
<style>
  :root {
    --magenta: #d6147f;
    --magenta-light: #ec4fa6;
    --magenta-deep: #b80f6c;
    --ink: #2a2a2a;
    --paper: #ffffff;
    --backdrop: #ece8e6;
    --photo-skin: #d9c2b3;
    --photo-warm: #8a6c58;
    --photo-dark: #3b2f29;
  }
  * { box-sizing: border-box; margin: 0; padding: 0; }
  html, body { width: 1200px; height: 913px; overflow: hidden; }
  body { background: var(--backdrop); position: relative; font-family: "Ubuntu", sans-serif; }

  .card {
    position: absolute;
    width: 560px;
    height: 320px;
    background: var(--paper);
    overflow: hidden;
    box-shadow: 0 10px 28px rgba(0,0,0,0.18);
  }

  /* Front */
  .card-front { left: 40px; top: 110px; }
  .corner-tab {
    position: absolute; right: 0; top: 0;
    width: 100px; height: 34px; background: var(--magenta);
  }
  .bottom-band {
    position: absolute; left: 0; right: 0; bottom: 0;
    height: 14px; background: var(--magenta);
  }
  .brand-name {
    position: absolute; left: 34px; top: 70px;
    font-family: "Ubuntu", sans-serif; font-weight: 300;
    font-size: 46px; letter-spacing: 2px; color: var(--magenta);
    text-transform: uppercase;
  }
  .contact-list {
    position: absolute; left: 300px; top: 142px;
    list-style: none;
    font-family: "Roboto Condensed", sans-serif;
    font-size: 15px; color: var(--ink);
  }
  .contact-list li { display: flex; align-items: center; gap: 10px; height: 25px; }
  .contact-icon { width: 14px; height: 14px; flex: none; }
  .holder { position: absolute; left: 34px; bottom: 48px; }
  .holder-name { font-weight: 700; font-size: 24px; color: var(--magenta); }
  .holder-role { font-family: "Ubuntu", sans-serif; font-weight: 700; font-size: 16px; color: var(--ink); margin-top: 4px; }

  /* Back */
  .card-back { left: 600px; top: 480px; }
  .photo-area {
    position: absolute; inset: 0;
    background: linear-gradient(120deg, var(--photo-warm) 0%, var(--photo-dark) 28%, var(--photo-skin) 58%, #efe3da 100%);
  }
  .services-band {
    position: absolute; left: 0; right: 0; bottom: 0; height: 96px;
    background: linear-gradient(90deg, var(--magenta-deep) 0%, var(--magenta-light) 55%, var(--magenta) 100%);
    padding: 14px 22px;
    font-family: "Roboto Condensed", sans-serif; font-weight: 700;
    font-size: 15px; line-height: 22px; color: var(--ink);
  }
</style>
</head>
<body>

<section class="card card-front" aria-label="Card front">
  <div class="corner-tab"></div>
  <div class="brand-name">The Velvet Magpie</div>

  <ul class="contact-list">
    <li>
      <svg class="contact-icon" viewBox="0 0 16 16" aria-hidden="true"><path fill="#d6147f" d="M3 1h3l1 4-2 1.5a9 9 0 0 0 4.5 4.5L11 9l4 1v3a2 2 0 0 1-2 2A12 12 0 0 1 1 3a2 2 0 0 1 2-2z"/></svg>
      0491802643
    </li>
    <li>
      <svg class="contact-icon" viewBox="0 0 16 16" aria-hidden="true"><rect x="1" y="3" width="14" height="10" fill="#d6147f"/><path d="M1.5 3.5 8 9l6.5-5.5" fill="none" stroke="#fff" stroke-width="1.3"/></svg>
      info@thevelvetmagpie-example.com
    </li>
    <li>
      <svg class="contact-icon" viewBox="0 0 16 16" aria-hidden="true"><circle cx="8" cy="8" r="7" fill="#d6147f"/><path d="M1 8h14M8 1v14M3 4.5h10M3 11.5h10" stroke="#fff" stroke-width="1" fill="none"/><ellipse cx="8" cy="8" rx="3" ry="7" fill="none" stroke="#fff" stroke-width="1"/></svg>
      www.thevelvetmagpie-example.com
    </li>
    <li>
      <svg class="contact-icon" viewBox="0 0 16 16" aria-hidden="true"><rect x="1" y="1" width="14" height="14" fill="#d6147f"/></svg>
      /thevelvetmagpie
    </li>
  </ul>

  <div class="holder">
    <div class="holder-name">Lorraine Kedby</div>
    <div class="holder-role">Professional Makeup Artist</div>
  </div>

  <div class="bottom-band"></div>
</section>

<section class="card card-back" aria-label="Card back">
  <div class="photo-area" role="img" aria-label="Photo of a woman applying eye makeup"></div>
  <div class="services-band">
    • Bridal makeup • Airbrush makeup • Special occasion • Formals<br>
    • Hens nights/ Girls night • Makeup lesson • Makeup for all ages from flower<br>
    girl to Nanna of the bride! • Photoshoot makeup • SPFX
  </div>
</section>

</body>
</html>
```